Harborline Lending and Capital. We provide MOSTLY residential home mortgages in Florida AND commercial loans for investment properties throughout the United states.
I would love to emulate so of the lender sites that are available on the internet but I would like to have the site as popular as possible for SEO purposes. Clients can already click the link to take them to the mortgage application where they can complete that and upload documents. If you could polish that up for me that would be great. I can also provide you with great detail on loan programs that are currently being offered. WE OFFER ALL MORTGAGE LENDING PRODUCTS. I would also like to add something in reference to the rate but I don't think it's legal to actually state or promise a rate for mortgage since they vary based on loan type, client and other criteria...

On the Harborline real estate site I would like to add a link or some way for clients to be able to put in credit card information to render services ...

Please let me know what you need from me

Thank you !!

Current link to site to improve and code

https://harborlinelendingandcapital.example/

Industry/Entity Type

Residential and commmercial lending

Coding

Coded - Design and coding required

Number of Pages Required

2 page

Requirements
Must have
• Love to integrate Mortgage interest rates even if general
Nice to have
• Link to fill out mortgage application via Quorvel LPX software

```html
<!DOCTYPE html>
<html lang="en">
<head>
<meta charset="utf-8">
<title>Harborline Lending and Capital</title>
<link href="https://fonts.googleapis.com/css2?family=Montserrat:wght@400;500;600;700;800&family=Poppins:wght@400;500;600;700&display=swap" rel="stylesheet">
<style>
:root{
  --green-dark:#1c3a20;
  --green-deep:#15301a;
  --lime:#9dbe3c;
  --lime-soft:#c4e2c6;
  --ink:#1e1e1e;
  --text:#3b3b3b;
  --grey-card:#f3f3f3;
  --footer:#0e170f;
  --white:#ffffff;
  --star:#f0a22a;
}
*{box-sizing:border-box;margin:0;padding:0}
html,body{width:1200px;height:4938px;overflow:hidden}
body{font-family:"Poppins",sans-serif;color:var(--text);background:var(--white);position:relative}
.abs{position:absolute}
.heading{font-family:"Montserrat",sans-serif;font-weight:700;color:var(--ink)}
.accent{color:var(--lime);text-decoration:underline;text-decoration-thickness:3px;text-underline-offset:6px;text-decoration-color:var(--green-dark)}
.photo{position:absolute;overflow:hidden}
.arrow-box{display:inline-flex;align-items:center;justify-content:center;background:#fff;border-radius:5px}
.btn-dark{position:absolute;display:flex;align-items:center;gap:10px;background:var(--green-dark);color:#fff;font-size:12px;border-radius:8px;padding:4px 4px 4px 12px;height:34px}
.btn-dark .arrow-box{width:28px;height:26px}
.btn-line{position:absolute;display:flex;align-items:center;gap:10px;background:#fff;color:var(--ink);border:2px solid var(--green-dark);font-size:12px;border-radius:8px;padding:3px 3px 3px 12px;height:34px}
.btn-line .arrow-box{width:28px;height:24px;background:#fff;border:1px solid var(--green-dark)}

/* header + hero */
.hero{position:absolute;left:0;top:0;width:1200px;height:635px}
.hero-photo{inset:0;background:linear-gradient(180deg,#0b130c 0%,#3d5233 18%,#5d6f4c 45%,#4a5f38 70%,#2f4526 100%)}
.hero-shade{position:absolute;inset:0;background:linear-gradient(90deg,rgba(10,20,10,.55),rgba(10,20,10,0) 60%)}
.brand{position:absolute;left:142px;top:8px;display:flex;align-items:center;gap:10px;color:#fff}
.brand-dot{width:58px;height:58px;border-radius:50%;background:#fff}
.brand-name{font-family:"Montserrat",sans-serif;font-weight:700;font-size:8px;letter-spacing:.4px;line-height:1.5;text-transform:uppercase}
.nav{position:absolute;top:28px;left:721px;display:flex;align-items:center;gap:28px;color:#fff;font-size:12px}
.nav-contact{background:var(--lime);border-radius:14px;padding:5px 16px;color:#fff}
.hero-title{position:absolute;left:167px;top:258px;color:#fff;font-family:"Montserrat",sans-serif;font-weight:800;font-size:53px;line-height:59px}
.hero-bar{position:absolute;left:142px;top:272px;width:7px;height:154px;background:var(--lime)}

/* general rate guide */
.rates{position:absolute;left:142px;top:470px;width:560px;padding:14px 18px;border-radius:12px;background:rgba(14,23,15,.62);border:1px solid rgba(157,190,60,.55);color:#fff}
.rates-head{display:flex;justify-content:space-between;align-items:center;font-size:13px;font-weight:600}
.rates-head span{background:var(--lime);color:var(--green-deep);border-radius:12px;padding:3px 12px;font-size:11px;font-weight:600}
.rates-list{display:flex;gap:8px;margin-top:10px;list-style:none}
.rates-list li{flex:1;text-align:center;font-size:11px;padding:6px 0;border-radius:6px;background:rgba(255,255,255,.1)}
.rates-note{margin-top:9px;font-size:10px;line-height:14px;color:#d6dcd3}

/* about */
.about-img-a{left:142px;top:704px;width:255px;height:366px;border-radius:12px;background:linear-gradient(160deg,#d7d4cd,#8c8474 55%,#3e3a33)}
.about-img-b{left:410px;top:704px;width:162px;height:245px;border-radius:12px;background:linear-gradient(160deg,#c9c7c2,#9a9186 60%,#56504a)}
.years{position:absolute;left:410px;top:966px;width:162px;height:104px;border-radius:12px;background:var(--green-dark);color:#fff;text-align:center;padding-top:18px}
.years b{display:block;font-size:32px;font-family:"Montserrat",sans-serif;font-weight:700;line-height:38px}
.years span{font-size:13px}
.about-eyebrow{left:613px;top:718px;color:var(--lime);font-size:15px}
.about-title{left:613px;top:742px;font-size:34px;line-height:40px;width:480px}
.about-copy{left:614px;top:834px;width:450px;font-size:12px;line-height:22.5px;color:var(--ink)}
.about-copy p+p{margin-top:8px}

/* loans */
.loans{position:absolute;left:0;top:1162px;width:1200px;height:519px;background:var(--green-dark)}
.loans-title{left:142px;top:120px;color:#fff;font-size:34px}
.loans-copy{left:142px;top:178px;width:340px;color:#e9efe6;font-size:12px;line-height:21px}
.loans-copy p+p{margin-top:14px}
.loan-card{position:absolute;top:86px;width:246px;height:339px;background:#fff;border-radius:12px 12px 48px 12px;text-align:center}
.loan-card .photo{left:0;top:0;width:246px;height:178px;border-radius:12px 12px 0 0}
.loan-card h3{position:absolute;left:32px;right:32px;top:160px;background:#fff;border-radius:10px 10px 0 0;padding-top:10px;font-family:"Poppins",sans-serif;font-weight:500;font-size:17px;color:var(--ink)}
.loan-card p{position:absolute;left:12px;right:12px;top:222px;font-size:12px;line-height:21px;text-align:left}
.loan-go{position:absolute;left:108px;bottom:-12px;width:28px;height:26px;background:var(--lime);border-radius:4px;display:flex;align-items:center;justify-content:center}

/* properties */
.props-band{position:absolute;left:0;top:1681px;width:1200px;height:403px;background:var(--lime)}
.props-title{left:0;width:1200px;top:1770px;text-align:center;font-size:34px}
.props-title .accent{color:var(--green-dark);text-decoration-color:var(--green-dark)}
.props-copy{left:290px;width:620px;top:1838px;text-align:center;font-size:12.5px;line-height:22px;color:var(--ink)}
.prop{position:absolute;width:217px;height:316px;border-radius:10px;overflow:hidden}
.prop::after{content:"";position:absolute;inset:0;background:linear-gradient(180deg,rgba(0,0,0,0) 55%,rgba(20,45,22,.9))}
.prop span{position:absolute;z-index:1;left:0;right:0;bottom:22px;text-align:center;color:#fff;font-size:14px;font-weight:500;text-decoration:underline}
.rule{position:absolute;left:0;width:1200px;height:1px;background:#dedede}

/* testimonials */
.section-title{left:0;width:1200px;text-align:center;font-size:34px}
.review{position:absolute;top:2626px;width:282px;height:182px;border-radius:14px;background:var(--grey-card);padding:20px 20px;font-size:12px;line-height:21px;color:var(--ink)}
.review.is-active{background:var(--green-dark);color:#fff}
.stars{color:var(--star);font-size:13px;letter-spacing:2px;height:30px;line-height:24px}
.quote-mark{position:absolute;right:20px;top:14px;font-family:"Montserrat",sans-serif;font-size:34px;line-height:30px;font-weight:700;font-style:italic;color:transparent;-webkit-text-stroke:1.2px #8a8a8a}
.review.is-active .quote-mark{color:#fff;-webkit-text-stroke:0}
.reviewer{position:absolute;top:2822px;display:flex;align-items:center;gap:12px;font-size:12.5px;color:var(--ink)}
.avatar{width:46px;height:46px;border-radius:50%;background:linear-gradient(160deg,#d9d3cc,#8e857d)}
.slider-btn{position:absolute;top:2700px;width:34px;height:34px;border-radius:50%;display:flex;align-items:center;justify-content:center}
.dot{position:absolute;top:2895px;width:14px;height:14px;border-radius:50%;border:1.5px solid var(--lime)}

/* blogs */
.blog{position:absolute;top:3161px;width:282px;height:414px;border-radius:14px;background:#fff;box-shadow:0 4px 14px rgba(0,0,0,.09)}
.blog .photo{left:0;top:0;width:282px;height:197px;border-radius:14px 14px 0 0}
.blog-date{position:absolute;left:91px;top:178px;width:100px;height:24px;background:#fff;border-radius:8px 8px 0 0;text-align:center;font-size:10.5px;line-height:26px;color:var(--ink)}
.blog h3{position:absolute;left:16px;top:218px;font-family:"Poppins",sans-serif;font-weight:600;font-size:17px;color:var(--ink)}
.blog p{position:absolute;left:16px;right:14px;top:254px;font-size:12px;line-height:21px}

/* contact */
.contact{position:absolute;left:142px;top:3721px;width:916px;height:506px;border-radius:22px;overflow:hidden;background:var(--lime-soft)}
.contact-photo{left:473px;top:0;width:443px;height:506px;background:linear-gradient(150deg,#f1f2f3,#b9bcc0 45%,#3c4553 75%,#26303c)}
.field-label{position:absolute;left:44px;font-size:12.5px;color:var(--ink)}
.field{position:absolute;left:38px;width:389px;height:42px;background:#fff;border-radius:4px}
.submit{position:absolute;left:38px;top:414px;width:389px;height:40px;background:var(--green-dark);color:#fff;font-size:13px;font-weight:600;letter-spacing:.5px;text-align:center;line-height:40px;border-radius:4px}

/* newsletter + footer */
.footer{position:absolute;left:0;top:4463px;width:1200px;height:475px;background:var(--footer)}
.newsletter{position:absolute;left:142px;top:4286px;width:916px;height:272px;background:var(--lime);border-radius:78px 78px 0 0;text-align:center}
.newsletter h2{position:absolute;left:0;right:0;top:58px;font-family:"Montserrat",sans-serif;font-weight:700;font-size:34px;color:var(--green-deep)}
.newsletter p{position:absolute;left:300px;right:300px;top:110px;font-size:12.5px;line-height:23px;color:var(--ink)}
.subscribe{position:absolute;left:188px;top:179px;width:540px;height:46px;background:#fff;border-radius:23px;overflow:hidden;display:flex;align-items:center}
.subscribe span{font-size:12px;color:#444;margin-left:14px}
.subscribe b{position:absolute;right:0;top:0;width:146px;height:46px;background:var(--green-deep);color:#fff;font-weight:500;font-size:12px;line-height:46px;border-radius:23px}
.f-col{position:absolute;top:4646px;color:#fff}
.f-col h4{font-family:"Poppins",sans-serif;font-weight:500;font-size:14px;letter-spacing:.3px;padding-bottom:8px;border-bottom:1px solid #6d746c;display:inline-block}
.f-links{list-style:none;margin-top:18px;font-size:12px}
.f-links li{display:flex;align-items:center;gap:8px;height:32px}
.f-links li::before{content:"";width:9px;height:9px;border:1px solid #cfd3cf;border-radius:50%}
.f-info{margin-top:16px;font-size:12px;line-height:17px}
.f-info div{display:flex;gap:12px;margin-bottom:14px}
.social{display:flex;align-items:center;gap:10px;height:38px;font-size:12px}
.social i{width:24px;height:24px;border:1.5px solid #fff;border-radius:50%}
.f-brand{position:absolute;left:774px;top:4640px;width:284px;color:#fff}
.f-brand .brand-name{font-size:7px}
.f-about{margin-top:22px;font-size:11.5px;line-height:18px;color:#e6e9e6}
.f-bottom{position:absolute;left:142px;right:142px;top:4884px;border-top:1px solid #8a9a3c;display:flex;justify-content:space-between;padding-top:16px;font-size:11.5px;color:#fff}
.f-bottom nav{display:flex;gap:20px}
</style>
</head>
<body>

<header class="hero">
  <div class="photo hero-photo" role="img" aria-label="Aerial view of a green Florida city with river, bridge and rolling hills"></div>
  <div class="hero-shade"></div>
  <div class="brand">
    <div class="brand-dot"></div>
    <div class="brand-name">Harborline Lending and Capital of Florida<br><span style="font-weight:500;letter-spacing:2px">Business and Commercial Division</span></div>
  </div>
  <nav class="nav">
    <span>Home</span><span>About Us</span><span>Properties</span><span class="nav-contact">Contact Us</span>
  </nav>
  <div class="hero-bar"></div>
  <h1 class="hero-title">Empowering<br>Homeownership,<br>Securing Investments</h1>
  <aside class="rates" aria-label="General mortgage rate guide">
    <div class="rates-head">Today's Mortgage Rate Guide <span>Check My Rate</span></div>
    <ul class="rates-list"><li>30-Yr Fixed</li><li>15-Yr Fixed</li><li>FHA / VA</li><li>Jumbo</li><li>Commercial</li></ul>
    <p class="rates-note">Rates are general market guides only and vary by loan type, credit profile and property. Not a commitment to lend.</p>
  </aside>
</header>

<section>
  <div class="photo about-img-a" role="img" aria-label="Two advisors reviewing loan documents at a desk"></div>
  <div class="photo about-img-b" role="img" aria-label="Smiling loan officer in a grey blazer"></div>
  <div class="years"><b>25+</b><span>Years of Experience</span></div>
  <div class="abs about-eyebrow">About</div>
  <h2 class="abs heading about-title">Harborline Lending and <span class="accent">Capital</span></h2>
  <div class="abs about-copy">
    <p>Harborline Lending Originates Residential Home loans in Florida and Commercial and business financing in all 50 States.</p>
    <p>We have over 25 years of experience in ALL types of real estate and commercial lending. We are strategically partnered to help you obtain ALL necessary components of residential and commercial lending. From the RIGHT lending partners to the best practice Insurance avenues and commercial and residential real estate partners</p>
  </div>
  <div class="btn-dark" style="left:613px;top:1017px">Read More <span class="arrow-box"><svg width="12" height="12" viewBox="0 0 12 12"><path d="M3 9 9 3M4 3h5v5" stroke="#1c3a20" stroke-width="1.4" fill="none"/></svg></span></div>
</section>

<section class="loans">
  <h2 class="abs heading loans-title" style="color:#fff">Types of <span class="accent" style="text-decoration-color:var(--lime)">Loans</span></h2>
  <div class="abs loans-copy">
    <p>Lorem ipsum dolor sit amet, consectetuer adipiscing elit, sed diam nonummy nibh euismod tincidunt ut.</p>
    <p>Diam nonummy nibh euismod tincidunt ut laoreet dolore magna aliquam erat volutpat. Ut wisi enim ad minim veniam, quis nostrud exerci tation ullamcorper suscipit lobortis nisl ut aliquip ex ea commodo consequat. Duis autem vel eum iriure dolor in hendrerit in vulputate velit esse molestie consequat, vel illum dolore eu feugiat nulla facilisis at vero eros eted.</p>
  </div>
  <article class="loan-card" style="left:544px">
    <div class="photo" style="background:linear-gradient(150deg,#e7e1d8,#b39a77 55%,#5b4a37)" role="img" aria-label="Small house model held over stacked coins"></div>
    <h3>Residential Loans</h3>
    <p>Lorem ipsum dolor sitted isnot for amet, consectetuer adipiscing elit, sedd diam nonummy nibh euismod tincidunt utted laoreet dolore.</p>
    <span class="loan-go"><svg width="12" height="12" viewBox="0 0 12 12"><path d="M3 9 9 3M4 3h5v5" stroke="#fff" stroke-width="1.4" fill="none"/></svg></span>
  </article>
  <article class="loan-card" style="left:813px">
    <div class="photo" style="background:linear-gradient(150deg,#eef0f1,#c7c9c4 50%,#8a8f87)" role="img" aria-label="Cash being handed over a laptop"></div>
    <h3>Commercial Loans</h3>
    <p>Lorem ipsum dolor sitted isnot for amet, consectetuer adipiscing elit, sedd diam nonummy nibh euismod tincidunt utted laoreet dolore.</p>
    <span class="loan-go"><svg width="12" height="12" viewBox="0 0 12 12"><path d="M3 9 9 3M4 3h5v5" stroke="#fff" stroke-width="1.4" fill="none"/></svg></span>
  </article>
</section>

<section>
  <div class="props-band"></div>
  <h2 class="abs heading props-title">Available <span class="accent">Properties</span></h2>
  <p class="abs props-copy">Lorem ipsum dolor sit amet, consectetuer adipiscing elit, sed diam nonummy nibh euismod tincidunt ut laoreet dolore magna aliquam erat volutpat. Ut wisi enim ad minim veniam.</p>
  <div class="prop" style="left:142px;top:1919px;background:linear-gradient(180deg,#cfd5da,#e9eaea 40%,#6f726f)" role="img" aria-label="Modern white house exterior"><span>12 Sunset Street</span></div>
  <div class="prop" style="left:376px;top:1990px;background:linear-gradient(180deg,#5f83a8,#2c3a45 40%,#151a1c)" role="img" aria-label="Dark modern house at dusk"><span>34 Union Avenue</span></div>
  <div class="prop" style="left:608px;top:1919px;background:linear-gradient(180deg,#7fa1c6,#c9ccc7 45%,#5e5c4e)" role="img" aria-label="Modern house with perforated facade"><span>56 Washington Street</span></div>
  <div class="prop" style="left:841px;top:1990px;background:linear-gradient(180deg,#86a8cf,#8e4a3c 40%,#404a55)" role="img" aria-label="Brick and metal modern house"><span>78 Oak Boulevard</span></div>
  <div class="btn-line" style="left:544px;top:2344px">View More <span class="arrow-box"><svg width="12" height="12" viewBox="0 0 12 12"><path d="M3 9 9 3M4 3h5v5" stroke="#1c3a20" stroke-width="1.4" fill="none"/></svg></span></div>
  <div class="rule" style="top:2467px"></div>
</section>

<section>
  <h2 class="abs heading section-title" style="top:2540px">Client <span class="accent">Testimonials</span></h2>
  <div class="slider-btn" style="left:90px;background:#e6e6e6"><svg width="10" height="10" viewBox="0 0 10 10"><path d="M6.5 1.5 3 5l3.5 3.5" stroke="#333" stroke-width="1.5" fill="none"/></svg></div>
  <div class="slider-btn" style="left:1074px;background:var(--green-dark)"><svg width="10" height="10" viewBox="0 0 10 10"><path d="M3.5 1.5 7 5 3.5 8.5" stroke="#fff" stroke-width="1.5" fill="none"/></svg></div>
  <article class="review" style="left:142px"><span class="quote-mark">99</span><div class="stars">★★★★★</div>Lorem ipsum dolor sitted for going to these ametted arett consectetuer ares adiping elitted thet, sedde diam staing nonummy nibh euismod arein. Lorem Ipsum has been the industry.</article>
  <article class="review is-active" style="left:458px"><span class="quote-mark">99</span><div class="stars">★★★★★</div>Lorem ipsum dolor sitted for going to these ametted arett consectetuer ares adiping elitted thet, sedde diam staing nonummy nibh euismod arein. Lorem Ipsum has been the industry.</article>
  <article class="review" style="left:776px"><span class="quote-mark">99</span><div class="stars">★★★★★</div>Lorem ipsum dolor sitted for going to these ametted arett consectetuer ares adiping elitted thet, sedde diam staing nonummy nibh euismod arein. Lorem Ipsum has been the industry.</article>
  <div class="reviewer" style="left:162px"><div class="avatar" role="img" aria-label="Portrait of client Dario Velman"></div>Dario Velman</div>
  <div class="reviewer" style="left:478px"><div class="avatar" role="img" aria-label="Portrait of client Lena Orsby"></div>Lena Orsby</div>
  <div class="reviewer" style="left:796px"><div class="avatar" role="img" aria-label="Portrait of client Tomas Reyker"></div>Tomas Reyker</div>
  <span class="dot" style="left:563px"></span>
  <span class="dot" style="left:593px;background:radial-gradient(circle,var(--green-dark) 45%,#fff 50%)"></span>
  <span class="dot" style="left:623px"></span>
  <div class="rule" style="top:2996px"></div>
</section>

<section>
  <h2 class="abs heading section-title" style="top:3073px">Our Latest <span class="accent">Blogs</span></h2>
  <article class="blog" style="left:142px">
    <div class="photo" style="background:linear-gradient(150deg,#eceae6,#b7aea3 55%,#4d4640)" role="img" aria-label="Business meeting around an office table"></div>
    <div class="blog-date">Nov 14, 2024</div>
    <h3>Title will come here...</h3>
    <p>Lorem ipsum dolor sitted isnot for amet, consectetuer adipiscing elit, sedd diam nonummy nibh euismod tincidunt utted laoreet dolore magna aliquam.</p>
    <div class="btn-line" style="left:88px;top:360px">Read More <span class="arrow-box"><svg width="12" height="12" viewBox="0 0 12 12"><path d="M3 9 9 3M4 3h5v5" stroke="#1c3a20" stroke-width="1.4" fill="none"/></svg></span></div>
  </article>
  <article class="blog" style="left:458px">
    <div class="photo" style="background:linear-gradient(180deg,#9fb4cc,#e9e6df 45%,#5d6b43)" role="img" aria-label="Large white house with lawn at sunset"></div>
    <div class="blog-date">Nov 14, 2024</div>
    <h3>Title will come here...</h3>
    <p>Lorem ipsum dolor sitted isnot for amet, consectetuer adipiscing elit, sedd diam nonummy nibh euismod tincidunt utted laoreet dolore magna aliquam.</p>
    <div class="btn-line" style="left:88px;top:360px">Read More <span class="arrow-box"><svg width="12" height="12" viewBox="0 0 12 12"><path d="M3 9 9 3M4 3h5v5" stroke="#1c3a20" stroke-width="1.4" fill="none"/></svg></span></div>
  </article>
  <article class="blog" style="left:776px">
    <div class="photo" style="background:linear-gradient(160deg,#c9d6dc,#b9a48d 50%,#4c5b4a)" role="img" aria-label="Family celebrating outside their new home"></div>
    <div class="blog-date">Nov 14, 2024</div>
    <h3>Title will come here...</h3>
    <p>Lorem ipsum dolor sitted isnot for amet, consectetuer adipiscing elit, sedd diam nonummy nibh euismod tincidunt utted laoreet dolore magna aliquam.</p>
    <div class="btn-line" style="left:88px;top:360px">Read More <span class="arrow-box"><svg width="12" height="12" viewBox="0 0 12 12"><path d="M3 9 9 3M4 3h5v5" stroke="#1c3a20" stroke-width="1.4" fill="none"/></svg></span></div>
  </article>
</section>

<section>
  <h2 class="abs heading section-title" style="top:3634px">Get in <span class="accent">Touch</span></h2>
  <div class="contact">
    <span class="field-label" style="top:48px">Name*</span><div class="field" style="top:70px"></div>
    <span class="field-label" style="top:128px">Email*</span><div class="field" style="top:150px"></div>
    <span class="field-label" style="top:208px">Phone*</span><div class="field" style="top:230px"></div>
    <span class="field-label" style="top:288px">Your Message*</span><div class="field" style="top:310px;height:86px"></div>
    <div class="submit">SUBMIT NOW</div>
    <div class="photo contact-photo" role="img" aria-label="Two advisors discussing documents at a laptop"></div>
  </div>
</section>

<footer>
  <div class="footer"></div>
  <div class="newsletter">
    <h2>Subscribe To Our Newsletter</h2>
    <p>Lorem Ipsum is simply dummyprinting typesetting industry. Lorem Ipsum has been</p>
    <div class="subscribe">
      <svg style="margin-left:22px" width="16" height="12" viewBox="0 0 16 12"><rect x="1" y="1" width="14" height="10" rx="1.5" fill="none" stroke="#333" stroke-width="1.3"/><path d="M1.5 1.5 8 7l6.5-5.5" fill="none" stroke="#333" stroke-width="1.3"/></svg>
      <span>Enter Your Email</span>
      <b>SUBSCRIBE NOW</b>
    </div>
  </div>

  <div class="f-col" style="left:142px">
    <h4>QUICK LINKS</h4>
    <ul class="f-links"><li>Home</li><li>About Us</li><li>Properties</li><li>Contact Us</li></ul>
  </div>
  <div class="f-col" style="left:311px">
    <h4>CONTACT DETAILS</h4>
    <div class="f-info">
      <div><svg width="12" height="16" viewBox="0 0 12 16"><path d="M6 15s5-5.6 5-9A5 5 0 0 0 1 6c0 3.4 5 9 5 9z" fill="#fff"/><circle cx="6" cy="6" r="1.8" fill="#0e170f"/></svg><span>0152 Palmcrest Way, Suite 4<br>Tampa Bay.</span></div>
      <div><svg width="13" height="13" viewBox="0 0 13 13"><path d="M3 1h2l1 3-1.5 1a7 7 0 0 0 3.5 3.5L9 7l3 1v2a2 2 0 0 1-2 2A10 10 0 0 1 1 3a2 2 0 0 1 2-2z" fill="#fff"/></svg><span>(555) 014-2290</span></div>
      <div><svg width="14" height="11" viewBox="0 0 14 11"><rect width="14" height="11" rx="1.5" fill="#fff"/><path d="M1 1.5 7 6l6-4.5" stroke="#0e170f" stroke-width="1.2" fill="none"/></svg><span>info@harborlinelending.example</span></div>
    </div>
  </div>
  <div class="f-col" style="left:611px">
    <h4>FOLLOW US</h4>
    <div style="margin-top:12px">
      <div class="social"><i></i>Friendspace</div>
      <div class="social"><i></i>Picturely</div>
      <div class="social"><i></i>Clipstream</div>
    </div>
  </div>
  <div class="f-brand">
    <div style="display:flex;align-items:center;gap:10px">
      <div class="brand-dot" style="width:62px;height:62px"></div>
      <div class="brand-name">Harborline Lending and Capital of Florida<br><span style="font-weight:500;letter-spacing:2px">Business and Commercial Division</span></div>
    </div>
    <p class="f-about">Lorem ipsum dolor sitte tincidunt utmost laoreet amet, consectet ueri adipiscing elit, sedden diam nonummy nibh euismod tincidunt utmost are in laoreet dolore mere ot app lok. <u>Read More</u></p>
  </div>
  <div class="f-bottom">
    <span>© 2025 Harborline Lending and Capital. All Rights Reserved.</span>
    <nav><span>Privacy Policy</span><span>|</span><span>Terms of Service</span></nav>
  </div>
</footer>

</body>
</html>
```